KRV Business Card

Looking for a business card for my restaurant group I own. Four different concepts:

Copperfield Alehouse
Bristow Alehouse
Tanager's Stone Hearth Kitchen
Pellston Patty Company

Card doesn't need to include all the logos.

```html
<!DOCTYPE html>
<html lang="en">
<head>
<meta charset="utf-8">
<title>KRV Business Card</title>
<link href="https://fonts.googleapis.com/css2?family=Lato:wght@400;700&display=swap" rel="stylesheet">
<style>
  :root {
    --backdrop: #2b2b2c;
    --card: #1e1f21;
    --card-back: #1b1c1e;
    --pattern: #242527;
    --gold: #d4ad5b;
    --grey: #8a8b8d;
    --white: #f2f2f2;
    --rule: #6b6c6e;
  }
  * { margin: 0; padding: 0; box-sizing: border-box; }
  html, body { width: 1200px; height: 1108px; overflow: hidden; }
  body {
    background: var(--backdrop);
    font-family: 'Lato', sans-serif;
    position: relative;
  }
  .card {
    position: absolute;
    top: 224px;
    width: 380px;
    height: 660px;
    border-radius: 22px;
    overflow: hidden;
  }
  .card-front { left: 180px; background: var(--card); text-align: center; }
  .card-back { left: 640px; background: var(--card-back); }

  .brand { margin-top: 96px; color: var(--gold); font-weight: 700; }
  .brand-initials { font-size: 76px; letter-spacing: 4px; line-height: 1; }
  .brand-name { font-size: 27px; letter-spacing: 3px; margin-top: 14px; line-height: 1.2; }

  .person { margin-top: 44px; }
  .person-name { color: var(--gold); font-size: 27px; font-weight: 700; }
  .person-role { color: var(--white); font-size: 17px; margin-top: 2px; }

  .icon-row {
    display: flex; align-items: center; justify-content: center;
    gap: 6px; margin: 14px 40px 0;
  }
  .icon-row .rule { flex: 1; height: 1px; background: var(--rule); }
  .icon-row svg { width: 24px; height: 24px; }

  .contact { color: var(--white); font-size: 18px; line-height: 1.45; margin-top: 10px; }
  .divider { height: 1px; background: var(--rule); margin: 12px 60px; }
  .address { color: var(--white); font-size: 18px; line-height: 1.4; }

  .back-pattern { position: absolute; inset: 0 0 240px 0; background: linear-gradient(180deg, var(--pattern), var(--card-back)); }
  .back-mark {
    position: absolute; right: 64px; top: 430px;
    color: var(--gold); font-weight: 700; font-size: 36px; letter-spacing: 2px;
  }
  .venues {
    position: absolute; left: 0; right: 0; top: 516px;
    text-align: center; color: #c9c9ca; font-size: 19px; font-weight: 700;
    text-transform: uppercase; line-height: 1.3; letter-spacing: 0.5px;
  }
</style>
</head>
<body>
  <section class="card card-front">
    <div class="brand">
      <div class="brand-initials">KRV</div>
      <div class="brand-name">KINROSS RIDGE<br>GROUP</div>
    </div>
    <div class="person">
      <div class="person-name">DANIEL WHITAKER</div>
      <div class="person-role">Managing Director</div>
    </div>
    <div class="icon-row">
      <span class="rule"></span>
      <svg viewBox="0 0 24 24" aria-label="Phone"><circle cx="12" cy="12" r="12" fill="var(--gold)"/><path d="M8 6.5c.6-.4 1.3-.3 1.6.3l.9 1.8c.2.5.1 1-.3 1.3l-.8.6c.5 1.3 1.6 2.5 3 3.1l.6-.8c.3-.4.9-.5 1.3-.3l1.8.9c.6.3.7 1 .3 1.6l-.7.9c-.5.6-1.3.8-2 .5-3-1.2-5.3-3.5-6.4-6.4-.3-.7-.1-1.5.5-2z" fill="var(--card)"/></svg>
      <svg viewBox="0 0 24 24" aria-label="Email"><circle cx="12" cy="12" r="12" fill="var(--gold)"/><rect x="6" y="8" width="12" height="8.5" fill="none" stroke="var(--card)" stroke-width="1.4"/><path d="M6 8l6 5 6-5" fill="none" stroke="var(--card)" stroke-width="1.4"/></svg>
      <svg viewBox="0 0 24 24" aria-label="Website"><circle cx="12" cy="12" r="12" fill="var(--gold)"/><circle cx="12" cy="12" r="6" fill="none" stroke="var(--card)" stroke-width="1.4"/><ellipse cx="12" cy="12" rx="2.6" ry="6" fill="none" stroke="var(--card)" stroke-width="1.2"/><path d="M6 12h12" stroke="var(--card)" stroke-width="1.2"/></svg>
      <span class="rule"></span>
    </div>
    <div class="contact">
      044-987 654 321<br>
      info@kinrossridge.com<br>
      www.kinrossridge.com
    </div>
    <div class="divider"></div>
    <div class="address">
      421, Address line here,<br>
      45452, Country Name
    </div>
  </section>

  <section class="card card-back">
    <div class="back-pattern" role="img" aria-label="Faint repeating brand pattern"></div>
    <div class="back-mark">KRV</div>
    <div class="venues">
      Copperfield Alehouse<br>
      Bristow Alehouse<br>
      Tanager's Stone Hearth Kitchen<br>
      Pellston Patty Company
    </div>
  </section>
</body>
</html>
```